Business Card Design for Bright Pebble

Bright Pebble is a company which caters to children .We provide clothes, shoes,kids furniture,room accessories,school bags,lunch boxes ,stationary etc for children ages 3-13.

Industry/Entity Type

Business

Contact Information for Business Card

Adetutu Ekanemi
CEO Bright Pebble
+2347051926384, +2348062417390
www.brightpebbleng.example
Instagram: brightpebbleng

Requirements
Must have
• Playful and colourful design.playful ,colourful text as well.
Nice to have
• Cartoon like drawings or graphics of happy,playful kids.

```html
<!DOCTYPE html>
<html lang="en">
<head>
<meta charset="utf-8">
<title>Bright Pebble – Business Card</title>
<link rel="stylesheet" href="https://fonts.googleapis.com/css2?family=Carlito:wght@400;700&display=swap">
<style>
  :root {
    --page-bg: #ffffff;
    --card-bg: #ffffff;
    --card-edge: #dedede;
    --ink: #231f20;
    --fun-magenta: #c81e9c;
    --fun-orange: #e8670f;
    --fun-green: #3f9e1c;
    --fun-blue: #1589c0;
    --fun-purple: #8a2ab0;
    --art-warm: #f9d7e8;
    --art-mid: #fbeeb8;
    --art-cool: #cdeef8;
  }
  * { box-sizing: border-box; margin: 0; padding: 0; }
  html, body {
    width: 1200px; height: 1200px; overflow: hidden;
    background: var(--page-bg);
  }
  body { position: relative; font-family: "Carlito", "Calibri", sans-serif; color: var(--ink); }

  .business-card {
    position: absolute;
    left: 301px; top: 403px;
    width: 597px; height: 385px;
    background: var(--card-bg);
    border: 1px solid var(--card-edge);
    overflow: hidden;
  }

  .kids-artwork {
    position: absolute;
    left: 397px; top: 0;
    width: 200px; height: 194px;
    background: linear-gradient(135deg, var(--art-warm), var(--art-mid) 50%, var(--art-cool));
  }

  .identity { position: absolute; left: 98px; top: 95px; }
  .person-name { font-size: 19px; font-weight: 400; line-height: 1.1; color: var(--fun-magenta); }
  .company-name { font-size: 13px; font-weight: 700; line-height: 1.3; color: var(--fun-orange); }

  .phones { position: absolute; left: 98px; top: 200px; list-style: none; color: var(--fun-green); }
  .phones li {
    font-size: 12px; line-height: 14px;
    display: flex; align-items: center; gap: 3px;
  }
  .phones svg { width: 9px; height: 9px; flex: none; }

  .web { position: absolute; left: 98px; top: 251px; }
  .website { font-size: 16px; font-weight: 700; line-height: 1.1; color: var(--fun-blue); }
  .social { font-size: 13.5px; line-height: 1.2; color: var(--fun-purple); }
</style>
</head>
<body>
  <main class="business-card">
    <div class="kids-artwork" role="img" aria-label="Illustration of a ring of cartoon children in colourful clothes holding hands"></div>

    <header class="identity">
      <p class="person-name">Adetutu Ekanemi CEO</p>
      <p class="company-name">Bright Pebble</p>
    </header>

    <ul class="phones">
      <li>
        <svg viewBox="0 0 10 10" aria-hidden="true"><path d="M2 1.2 3.6 3 2.9 4.1c.6 1.3 1.6 2.3 2.9 2.9L6.9 6.3 8.8 8 8 9C4.5 9 1 5.5 1 2z" fill="currentColor"/></svg>
        + 234 705 192 6384
      </li>
      <li>
        <svg viewBox="0 0 10 10" aria-hidden="true"><path d="M2 1.2 3.6 3 2.9 4.1c.6 1.3 1.6 2.3 2.9 2.9L6.9 6.3 8.8 8 8 9C4.5 9 1 5.5 1 2z" fill="currentColor"/></svg>
        + 234 806 241 7390
      </li>
    </ul>

    <div class="web">
      <p class="website">www.brightpebbleng.example</p>
      <p class="social">Instagram.brightpebbleng</p>
    </div>
  </main>
</body>
</html>
```